Business Card Design Competition

We need a business card design for our Internet Marketing company. We require both front and back designs and the final card must be 89x53mm in size, plus crop marks to 91x55mm. Colours as per logo, plus perhaps black and/or grey (#828282).
Final text must be editable (if you can supply an editable Fireworks PNG, even better)...
FRONT TEXT:
Full Name
Position
Address Line
Suburb, State, Postcode
Phone: 0000 000 000
Mobile: 0000 000 000
Email: xxx@brightlanemedia.com.au
Web: www.brightlanemedia.com.au
Rear of card should be a fresh design plus our slogan text: "Getting You Noticed" in large font, then in small text "Kestrel Holdings Pty Ltd (ABN: 42 561 903 774)".
Target Market(s)
Small/Medium Businesses
Industry/Entity Type
Business

```html
<!DOCTYPE html>
<html lang="en">
<head>
<meta charset="utf-8">
<title>Brightlane Media – Business Card</title>
<link rel="stylesheet" href="https://fonts.googleapis.com/css2?family=Questrial&family=Open+Sans:wght@400&display=swap">
<style>
  :root {
    --orange: #f7941d;
    --green: #8dc63f;
    --green-pale: #e4f1d2;
    --ink: #1a1a1a;
    --card-edge: #9a9a9a;
    --card-top: #ffffff;
    --card-bottom: #eeeeee;
    --page: #ffffff;
  }
  html, body {
    margin: 0;
    padding: 0;
    width: 970px;
    height: 1200px;
    overflow: hidden;
    background: var(--page);
  }
  .canvas {
    position: relative;
    width: 970px;
    height: 1200px;
  }
  .card {
    position: absolute;
    left: 6px;
    width: 956px;
    border: 2px solid var(--card-edge);
    border-radius: 34px;
    overflow: hidden;
    background: linear-gradient(180deg, var(--card-top) 0%, var(--card-bottom) 100%);
    box-shadow: 0 3px 6px rgba(0,0,0,0.25);
  }
  .card--front { top: 6px; height: 568px; }
  .card--back { top: 590px; height: 602px; }

  .card__band {
    position: absolute;
    left: 0;
    right: 0;
    bottom: 0;
    height: 56px;
    background: var(--green);
  }

  .front__backdrop-disc {
    position: absolute;
    left: 440px;
    top: 20px;
    width: 460px;
    height: 460px;
    border-radius: 50%;
    background: var(--green);
    opacity: 0.12;
  }
  .brand {
    position: absolute;
    left: 40px;
    top: 120px;
    display: flex;
    align-items: center;
    gap: 36px;
  }
  .brand__disc {
    width: 300px;
    height: 300px;
    border-radius: 50%;
    background: var(--orange);
    flex: none;
  }
  .brand__name {
    font-family: "Questrial", "Century Gothic", sans-serif;
    color: var(--orange);
    font-weight: 400;
    line-height: 1;
    margin: 0;
  }
  .brand__name span { display: block; }
  .brand__name .brand__line-one { font-size: 108px; }
  .brand__name .brand__line-two { font-size: 88px; margin-top: 8px; padding-left: 90px; }

  .back__pattern {
    position: absolute;
    inset: 0 0 56px 0;
    background: linear-gradient(135deg, #fdf1e2 0%, var(--green-pale) 100%);
    opacity: 0.7;
  }
  .contact {
    position: absolute;
    left: 90px;
    top: 108px;
    margin: 0;
    font-family: "Open Sans", Arial, sans-serif;
    font-size: 29px;
    line-height: 33px;
    color: var(--ink);
  }
  .contact__group { margin: 0 0 48px 0; }
  .contact__group p { margin: 0; }
</style>
</head>
<body>
<main class="canvas">
  <section class="card card--front">
    <div class="front__backdrop-disc" aria-hidden="true"></div>
    <div class="brand">
      <div class="brand__disc" aria-hidden="true"></div>
      <h1 class="brand__name">
        <span class="brand__line-one">Brightlane</span>
        <span class="brand__line-two">Media</span>
      </h1>
    </div>
    <div class="card__band"></div>
  </section>

  <section class="card card--back">
    <div class="back__pattern" role="img" aria-label="Faint repeating pattern of the company mark and name across the card"></div>
    <div class="contact">
      <div class="contact__group">
        <p class="contact__name">Full Name</p>
        <p class="contact__position">Position</p>
      </div>
      <div class="contact__group">
        <p>Address Line</p>
        <p>Suburb, State, Postcode</p>
      </div>
      <div class="contact__group">
        <p>Phone: 0000 000 000</p>
        <p>Mobile: 0000 000 000</p>
      </div>
      <div class="contact__group">
        <p>Email: xxx@brightlanemedia.com.au</p>
        <p>Web: www.brightlanemedia.com.au</p>
      </div>
    </div>
    <div class="card__band"></div>
  </section>
</main>
</body>
</html>
```